Vantoq Business Card Project showing the logo and a marbo image on the rear

Design a whacky but professional business card, the logo is for the front and the Marbo image is for the rear. Happy to consider other open source Marbo Images if the designer wants to select one from the web. Vantoq is a competitor to OMB.com.au and Pellory.com.au and is based around every property in Australia

Target Market(s)

Business

Contact Information for Business Card

Name, Title, Email, Web, Phone Number

Font styles to use
Other font styles liked:
• avenir

Requirements
Must have
• Image on Back logo on front
Nice to have
• Happy to consider other images on rear, preftably Colin Marbo. Image supplied I own, we can use open source other Marbo Images

```html
<!DOCTYPE html>
<html lang="en">
<head>
<meta charset="utf-8">
<title>Vantoq Business Card</title>
<link rel="stylesheet" href="https://fonts.googleapis.com/css2?family=Montserrat:wght@700&family=Nunito+Sans:wght@400;600;800&display=swap">
<style>
  :root {
    --page: #232323;
    --card-black: #1c1c1c;
    --orange: #f5911e;
    --white: #ffffff;
    --sky: #3c8fe0;
    --night: #2a4fb0;
    --warm: #e8612c;
    --sun: #f3c32a;
    --leaf: #2f7d3a;
  }
  * { margin: 0; padding: 0; box-sizing: border-box; }
  html, body { width: 1200px; height: 988px; overflow: hidden; }
  body {
    background: var(--page);
    font-family: "Nunito Sans", sans-serif;
    position: relative;
  }
  .card {
    position: absolute;
    width: 700px;
    height: 400px;
    border-radius: 22px;
    overflow: hidden;
    box-shadow: 0 12px 30px rgba(0,0,0,.45);
  }
  .card--artwork { left: 250px; top: 64px; }
  .card--details { left: 250px; top: 524px; background: var(--card-black); }

  .artwork {
    position: absolute; inset: 0;
    background:
      linear-gradient(180deg, rgba(60,143,224,.0) 0%, rgba(0,0,0,.0) 40%),
      linear-gradient(120deg, var(--sky) 0%, var(--night) 28%, var(--leaf) 48%, var(--warm) 66%, var(--sun) 82%, #2fa6c8 100%);
  }
  .artwork::after {
    content: ""; position: absolute; inset: 0;
    background: linear-gradient(180deg, rgba(255,255,255,.12) 0%, rgba(0,0,0,.25) 100%);
  }

  .brand {
    position: absolute;
    display: flex; align-items: center; gap: 14px;
  }
  .brand__mark {
    width: 44px; height: 44px;
    background: var(--orange);
  }
  .brand__name {
    font-family: "Montserrat", sans-serif;
    font-weight: 700;
    color: var(--white);
    font-size: 62px;
    letter-spacing: 1px;
    line-height: 1;
  }
  .card--artwork .brand { left: 50%; top: 50%; transform: translate(-50%, -50%); }
  .card--details .brand { left: 50%; top: 70px; transform: translateX(-50%); }

  .person {
    position: absolute;
    right: 378px; top: 218px;
    text-align: right;
  }
  .person__name {
    color: var(--orange);
    font-weight: 800;
    font-size: 25px;
    letter-spacing: .5px;
    text-transform: uppercase;
  }
  .person__title {
    color: var(--white);
    font-size: 18px;
    margin-top: 2px;
  }
  .divider {
    position: absolute;
    left: 340px; top: 205px;
    width: 1px; height: 80px;
    background: var(--orange);
  }
  .contact {
    position: absolute;
    left: 362px; top: 204px;
    list-style: none;
  }
  .contact__item {
    display: flex; align-items: center; gap: 10px;
    color: var(--white);
    font-size: 17px;
    line-height: 27px;
  }
  .contact__icon { width: 13px; height: 13px; flex: none; }
  .contact__accent { color: var(--orange); }
  .address-band {
    position: absolute;
    left: 0; right: 0; top: 308px;
    height: 40px;
    background: var(--orange);
    color: var(--white);
    font-size: 19px;
    display: flex; align-items: center; justify-content: center;
  }
</style>
</head>
<body>

<section class="card card--artwork">
  <div class="artwork" role="img" aria-label="Colourful naive-art city illustration of bright buildings under a blue sky with clouds and stars"></div>
  <div class="brand">
    <span class="brand__mark"></span>
    <span class="brand__name">Vantoq</span>
  </div>
</section>

<section class="card card--details">
  <div class="brand">
    <span class="brand__mark"></span>
    <span class="brand__name">Vantoq</span>
  </div>

  <div class="person">
    <p class="person__name">Evan Corliss</p>
    <p class="person__title">Executive Producer</p>
  </div>

  <span class="divider"></span>

  <ul class="contact">
    <li class="contact__item">
      <svg class="contact__icon" viewBox="0 0 16 16"><path fill="#f5911e" d="M3 1l3 3-2 2c1 2 3 4 5 5l2-2 3 3-2 3C6 15 1 10 1 3z"/></svg>
      555-210-4471
    </li>
    <li class="contact__item">
      <svg class="contact__icon" viewBox="0 0 16 16"><rect x="1" y="3" width="14" height="10" fill="#f5911e"/><path d="M1 3l7 6 7-6" fill="none" stroke="#1c1c1c" stroke-width="1.5"/></svg>
      Evan@vantoq.com.au
    </li>
    <li class="contact__item">
      <svg class="contact__icon" viewBox="0 0 16 16"><circle cx="8" cy="8" r="7" fill="#f5911e"/><path d="M1 8h14M8 1c3 3 3 11 0 14M8 1c-3 3-3 11 0 14" fill="none" stroke="#1c1c1c" stroke-width="1.2"/></svg>
      <span>www.<span class="contact__accent">vantoq</span>.com.au</span>
    </li>
  </ul>

  <div class="address-band">1840 W Harlow street Denmore County name 4172</div>
</section>

</body>
</html>
```